email presentation and marketing

we need a email to be used to present our company and services to potential customer. it needs to contain our logo, address, details about our company, photos and a well described text about our work .
I will send a web site from one of the company we are targeting.
The e mail must be sober, elegant, persuasive. The client needs to have the feeling it is dealing to a big company.
See below one of out potential clients
http://qrvdwellings.com/

Target Market(s)

High end custom homes

Industry/Entity Type

Painting And Decorating

Font styles to use
Serif
Sans Serif

Requirements
Must have
• Our name, location, portfolio (need to send some pics), web site http://kb-coatingworks.com.
• Need to develop a email to present our company to potential clients.
Nice to have
• clients reviews.
• we are listed on nest ratings. https://nestratings.com/companies/5831046-kb-custom?service_area=7420561
Should not have
• not colorful

```html
<!DOCTYPE html>
<html lang="en">
<head>
<meta charset="utf-8">
<title>KB Coating Works – Introduction</title>
<link rel="stylesheet" href="https://fonts.googleapis.com/css2?family=Roboto:ital,wght@0,400;0,500;0,700;1,400&display=swap">
<style>
:root{
  --ink:#1f1f1f;
  --muted:#555;
  --paper:#efefef;
  --dark:#252628;
  --darker:#3a3b3d;
  --gold:#e3c102;
  --white:#fff;
  --ring:#b9b9b9;
}
*{box-sizing:border-box;margin:0;padding:0}
html,body{width:1200px;height:3041px;overflow:hidden;background:var(--dark);font-family:"Roboto",sans-serif;color:var(--ink)}
.email{position:relative;width:1200px;height:3041px}

/* masthead */
.masthead{position:absolute;left:0;top:0;width:1200px;height:251px;background:var(--paper)}
.brand{position:absolute;left:250px;top:72px;width:270px;display:flex;flex-direction:column;align-items:center;gap:14px}
.brand-mark{display:block;width:44px;height:44px;background:var(--gold)}
.brand-name{font-size:32px;font-weight:700;color:var(--gold);white-space:nowrap;line-height:1}
.contact{position:absolute;right:221px;top:42px;text-align:right;font-size:17px;line-height:22px;color:var(--ink)}
.contact .phone{font-size:23px;line-height:28px;margin-bottom:36px}
.contact .addr{margin-bottom:20px}

/* intro */
.intro-band{position:absolute;left:0;top:251px;width:1200px;height:1082px;background:var(--dark)}
.side-photo{position:absolute;top:300px;width:34px;height:572px}
.side-left{left:0;background:linear-gradient(90deg,#2b2c2e,#6d6e70)}
.side-right{right:0;background:linear-gradient(90deg,#6d6e70,#2b2c2e)}
.hero{position:absolute;left:34px;top:300px;width:1134px;height:627px;
  background:linear-gradient(180deg,#8e9398 0%,#b3b6b9 18%,#c9ccce 28%,#5b5e61 36%,#8f8a82 44%,#a49d92 55%,#6e6a65 66%,#d9dcdf 72%,#eef0f2 85%,#f7f8f9 100%)}
.title-bar{position:absolute;left:223px;top:876px;width:756px;height:51px;background:var(--gold);color:var(--ink);font-size:27px;font-weight:700;line-height:51px;padding-left:32px;letter-spacing:.3px;white-space:nowrap}
.intro-card{position:absolute;left:223px;top:927px;width:756px;height:320px;background:var(--white);border-radius:0 0 16px 16px;display:flex;padding:22px 30px 30px}
.intro-text{width:470px;font-size:20px;line-height:32px;color:#333;padding-right:24px}
.services{border-left:1px solid #e4e4e4;padding-left:18px;padding-top:10px;list-style:none;font-size:18px;font-weight:700;line-height:24px;color:var(--ink);letter-spacing:.4px}
.services li{margin-bottom:32px}
.services li:first-child{margin-bottom:34px}

.cta{position:absolute;left:444px;width:312px;height:48px;border-radius:24px;background:var(--gold);color:var(--ink);font-size:23px;font-weight:500;text-align:center;line-height:48px}
.cta-top{top:1271px}

/* testimonials */
.testimonials{position:absolute;left:0;top:1333px;width:1200px;height:762px;background:var(--paper)}
.section-title{position:absolute;left:0;width:1200px;text-align:center;font-size:30px;font-weight:500;line-height:36px}
.testimonials .section-title{top:31px;color:var(--ink)}
.review{position:absolute;top:102px;width:380px;text-align:center}
.review-a{left:222px}
.review-b{left:598px}
.avatar{display:block;margin:0 auto}
.reviewer{margin-top:14px;font-size:19px;line-height:22px;color:#444}
.reviewer.italic{font-style:italic}
.job{margin-top:29px;font-size:16px;line-height:20px;color:#444}
.quote{margin-top:20px;font-size:15px;font-style:italic;line-height:20px;color:#666}
.photo{position:absolute;top:392px;width:349px;height:345px}
.photo-a{left:237px;background:linear-gradient(180deg,#f2f2f2 0%,#c9c7c6 12%,#8f8c8b 30%,#b2aeab 42%,#6f6a66 55%,#2b2a2c 68%,#3d3c3e 78%,#e9e8e7 88%,#f6f6f6 100%)}
.photo-b{left:616px;background:linear-gradient(180deg,#f1efed 0%,#d8d1ca 14%,#cfc7bf 26%,#3c3a39 40%,#4a4846 62%,#8c857e 74%,#6f6a65 86%,#a39b93 100%)}

/* works */
.works{position:absolute;left:0;top:2095px;width:1200px;height:875px;background:var(--dark)}
.works .section-title{top:20px;color:var(--white)}
.work{position:absolute;top:100px;width:145px;height:237px}
.work-1{left:245px;background:linear-gradient(180deg,#b8b4ad 0%,#d9d6d0 25%,#eeece8 50%,#c7c4be 75%,#a9a59f 100%)}
.work-2{left:433px;background:linear-gradient(180deg,#eaeaea 0%,#cfcfcf 30%,#3b3634 55%,#1f1d1d 75%,#8a8787 100%)}
.work-3{left:622px;background:linear-gradient(180deg,#dcd8d3 0%,#b7afa6 35%,#6b4a35 60%,#3e2a1e 80%,#2a1c14 100%)}
.work-4{left:812px;background:linear-gradient(180deg,#a8a39c 0%,#8d8278 30%,#b0a799 50%,#6a625a 70%,#ecebe8 85%,#f4f4f3 100%)}
.cta-bottom{top:383px}

.footer-brand{position:absolute;left:0;top:500px;width:1200px;display:flex;flex-direction:column;align-items:center;gap:10px}
.footer-brand .brand-mark{width:36px;height:36px}
.footer-brand .brand-name{font-size:27px}
.footer-info{position:absolute;left:0;top:626px;width:1200px;text-align:center;font-size:21px;line-height:26px;color:var(--white)}
.social{position:absolute;left:0;top:798px;width:1200px;display:flex;justify-content:center;gap:16px}
.social span{display:block;width:48px;height:48px;border:2px solid var(--ring);border-radius:50%;background:#2f3033}

.legal{position:absolute;left:0;top:2970px;width:1200px;height:71px;background:var(--darker);color:var(--white);font-size:20px;text-align:center;line-height:71px}
</style>
</head>
<body>
<div class="email">

  <header class="masthead">
    <div class="brand"><span class="brand-mark"></span><span class="brand-name">KB Coating Works</span></div>
    <div class="contact">
      <p class="phone">Ph: 416 555 0192</p>
      <p class="addr">A: 58 Alderwood Cres, Unit C2 &nbsp;|&nbsp; M4K 2R7<br>Toronto | Ontario</p>
      <p>info@coatingworkspro.com<br>http://coatingworkspro.com/</p>
    </div>
  </header>

  <section class="intro-band"></section>
  <div class="side-photo side-left" role="img" aria-label="Edge of a neighbouring house photo"></div>
  <div class="side-photo side-right" role="img" aria-label="Edge of a neighbouring house photo"></div>
  <div class="hero" role="img" aria-label="Photo of a large stone custom home with a turret, under winter snow"></div>
  <h1 class="title-bar">KB COATING – WE ARE ALWAYS READY TO SERVE</h1>
  <div class="intro-card">
    <p class="intro-text">K.B Coating Works is a Toronto based company that provides customised home painting, commercial and industrial painting services to Greater Toronto and metropolitan cities. We use modern equipment and superior brand materials to deliver a high-quality work which makes us nothing less then proud.</p>
    <ul class="services">
      <li>- WALLPAPER<br>INSTALLATION</li>
      <li>- SPRAY FINISH</li>
      <li>- DRYWALL REPAIRS</li>
      <li>- STAIRCASE FINISH</li>
    </ul>
  </div>
  <div class="cta cta-top">GET A QUOTE</div>

  <section class="testimonials">
    <h2 class="section-title">CLIENT TESTIMONIALS</h2>
    <div class="review review-a">
      <svg class="avatar" width="74" height="74" viewBox="0 0 74 74" aria-hidden="true"><circle cx="37" cy="37" r="37" fill="#111"/><circle cx="37" cy="28" r="12" fill="#fff"/><path d="M14 58a23 18 0 0 1 46 0a30 30 0 0 1-46 0z" fill="#fff"/></svg>
      <p class="reviewer italic">TOMAS</p>
      <p class="job">Paint Of &nbsp;New Homes and Renovations</p>
      <p class="quote">Marcus and his staff are reliable, provide great<br>quality and service. myself and my clients are<br>extremely satisfied with his work.</p>
    </div>
    <div class="review review-b">
      <svg class="avatar" width="74" height="74" viewBox="0 0 74 74" aria-hidden="true"><circle cx="37" cy="37" r="37" fill="#111"/><circle cx="37" cy="28" r="12" fill="#fff"/><path d="M14 58a23 18 0 0 1 46 0a30 30 0 0 1-46 0z" fill="#fff"/></svg>
      <p class="reviewer">Brevcon Inc</p>
      <p class="job">Painting Of New Home</p>
      <p class="quote">Contractor was hired to paint New home. Staff<br>was friendly, courteous, helpful, clean,<br>proactive, reliable.</p>
    </div>
    <div class="photo photo-a" role="img" aria-label="Photo of a finished bedroom with patterned feature wallpaper"></div>
    <div class="photo photo-b" role="img" aria-label="Photo of a freshly painted living room with fireplace and tall windows"></div>
  </section>

  <section class="works">
    <h2 class="section-title">OUR WORKS</h2>
    <div class="work work-1" role="img" aria-label="Photo of a bright bathroom with arched windows and freestanding tub"></div>
    <div class="work work-2" role="img" aria-label="Photo of a curved staircase with dark finish"></div>
    <div class="work work-3" role="img" aria-label="Photo of a painted hallway with wood floors"></div>
    <div class="work work-4" role="img" aria-label="Photo of a stone fireplace wall in a finished room"></div>
    <div class="cta cta-bottom">GET A QUOTE</div>
    <div class="footer-brand"><span class="brand-mark"></span><span class="brand-name">KB Coating Works</span></div>
    <div class="footer-info">
      <p>KB Coating Works</p>
      <p>Contact: Marcus Delaney</p>
      <p>416 555 0192|kbcoatingworks12@mailbox.com</p>
      <p>kb-coatingworks.com</p>
    </div>
    <div class="social" role="img" aria-label="Social media links">
      <span></span><span></span><span></span><span></span><span></span>
    </div>
  </section>

  <footer class="legal">KB Coating Works © All rights reserved</footer>
</div>
</body>
</html>
```